Home Loan Introducer needs logo/business cards

We need a simple but classy logo for business cards and flyers. The business is a home loan referral business that is called an Introducer. The business name is "The Harborline".
I was thinking very simple and straight to the point on the front with "Home Loans" the only thing on the front with a nice background colour/s.
Then on the back, "The Harborline"
and "Quality Customer Service"
and "Email, text or call welcome"
and then my name, email address and phone number.
Updates
Thank you for all the designs :-)
Target Market(s)
Home buyers.
Home owners.
Investors.
Industry/Entity Type
Loan
Look and feel

```html
<!DOCTYPE html>
<html lang="en">
<head>
<meta charset="utf-8">
<title>The Harborline – Business Cards</title>
<link rel="stylesheet" href="https://fonts.googleapis.com/css2?family=Exo+2:wght@500;600;700;800&display=swap">
<style>
  :root {
    --backdrop: #e8e8eb;
    --card-black: #1f1f20;
    --brand-orange: #fbb03b;
    --orange-light: #fdc870;
    --brand-blue: #1466c2;
    --ink-dark: #2a2116;
    --white: #ffffff;
    --ghost: #2c2c2d;
  }
  * { box-sizing: border-box; margin: 0; padding: 0; }
  html, body {
    width: 1200px; height: 848px; overflow: hidden;
    background: var(--backdrop);
    font-family: "Exo 2", sans-serif;
  }
  .stage { position: relative; width: 1200px; height: 848px; }

  .card {
    position: absolute; top: 124px;
    width: 380px; height: 600px;
    background: var(--card-black);
    overflow: hidden;
    box-shadow: 0 14px 30px rgba(0,0,0,.18);
  }
  .card--front { left: 170px; }
  .card--back  { left: 650px; }

  /* rotated frame: text reads top to bottom, letter tops face right */
  .turned {
    position: absolute;
    width: 600px; height: 380px;
    left: -110px; top: 110px;
    transform: rotate(90deg);
  }

  /* front */
  .front-houses {
    position: absolute; left: 170px; top: 120px;
    width: 140px; height: 300px;
    background: linear-gradient(180deg, var(--ghost), #262627);
    border-radius: 6px;
  }
  .front-band {
    position: absolute; left: 78px; top: 60px;
    width: 94px; height: 480px;
    background: var(--brand-orange);
    border-radius: 10px;
  }
  .headline {
    position: absolute; left: 60px; top: 208px;
    width: 480px; height: 94px;
    display: flex; align-items: center; justify-content: center; gap: 20px;
    font-weight: 800; font-size: 76px; letter-spacing: 1px; line-height: 1;
  }
  .headline__home { color: var(--white); }
  .headline__loan { color: var(--brand-blue); }

  /* back */
  .back-panel {
    position: absolute; left: 0; top: 0;
    width: 250px; height: 600px;
    background: var(--brand-orange);
  }
  .back-house {
    position: absolute; left: 20px; top: 0;
    width: 230px; height: 150px;
    background: linear-gradient(160deg, var(--orange-light), var(--brand-orange));
  }
  .brand-dot {
    position: absolute; left: 280px; top: 100px;
    width: 44px; height: 44px; border-radius: 50%;
    background: var(--brand-blue);
  }
  .brand-label {
    position: absolute; left: 150px; top: 112px;
    height: 36px; padding: 0 12px;
    background: var(--brand-orange);
    border-radius: 4px;
    display: flex; align-items: center;
    font-weight: 700; font-size: 22px; letter-spacing: .5px;
    color: var(--brand-blue); white-space: nowrap;
  }
  .perks {
    position: absolute; left: 262px; top: 160px;
    list-style: none;
    font-weight: 600; font-size: 16px; color: var(--brand-blue); line-height: 24px;
  }
  .perks li { display: flex; align-items: center; gap: 4px; }
  .perks svg { width: 16px; height: 16px; }
  .rule {
    position: absolute; height: 2px; background: var(--white);
  }
  .rule--top { left: 230px; top: 212px; width: 170px; }
  .rule--bottom { left: 222px; top: 300px; width: 200px; }
  .contact-name {
    position: absolute; left: 262px; top: 216px;
    font-weight: 700; font-size: 26px; color: var(--brand-blue);
  }
  .contact-lines {
    position: absolute; left: 236px; top: 252px;
    font-weight: 600; font-size: 11px; line-height: 16px; color: var(--ink-dark);
  }
</style>
</head>
<body>
<main class="stage">

  <section class="card card--front" aria-label="Card front">
    <div class="front-houses" role="img" aria-label="Faint row of house silhouettes"></div>
    <div class="front-band"></div>
    <div class="turned">
      <h1 class="headline"><span class="headline__home">HOME</span><span class="headline__loan">LOAN</span></h1>
    </div>
  </section>

  <section class="card card--back" aria-label="Card back">
    <div class="back-panel"></div>
    <div class="back-house" role="img" aria-label="Large faint house outline"></div>
    <span class="brand-dot"></span>
    <div class="turned">
      <div class="brand-label">THE HARBORLINE</div>
      <ul class="perks">
        <li><svg viewBox="0 0 16 16"><path d="M2 9l4 4 8-10" fill="none" stroke="#1f1f20" stroke-width="2"/></svg>Quality Customer Service</li>
        <li><svg viewBox="0 0 16 16"><path d="M2 9l4 4 8-10" fill="none" stroke="#1f1f20" stroke-width="2"/></svg>Email, text or call welcome</li>
      </ul>
      <span class="rule rule--top"></span>
      <p class="contact-name">Dalton Prewitt</p>
      <p class="contact-lines">Phone: +61 400 555 218<br>Email: hello@harborline.com</p>
      <span class="rule rule--bottom"></span>
    </div>
  </section>

</main>
</body>
</html>
```